Redesign of business card for Cedar Ridge Mechanical

We are looking for a new design for our business cards for Cedar Ridge Mechanical. We are a plumbing & HVAC construction company, operating on the West Coast of Canada and USA. Logo attached.
Industry/Entity Type
Construction - Plumbing & HVAC
Contact Information for Business Card
Name, address, phone numbers, email, website address
Look and feel
Each slider illustrates characteristics of the customer's brand and the style your logo design should communicate.

```html
<!DOCTYPE html>
<html lang="en">
<head>
<meta charset="UTF-8">
<title>Cedar Ridge Mechanical — Business Card</title>
<link href="https://fonts.googleapis.com/css2?family=Montserrat:wght@400;500;700&display=swap" rel="stylesheet">
<style>
  :root {
    --stage: #d9d9d9;
    --card-dark: #2a2a2a;
    --card-light: #ffffff;
    --ink: #1e1e1e;
    --ink-soft: #2f2f2f;
    --on-dark: #ffffff;
  }
  * { box-sizing: border-box; margin: 0; padding: 0; }
  html, body {
    width: 1200px; height: 985px; overflow: hidden;
    background: var(--stage);
    font-family: "Montserrat", sans-serif;
  }
  .stage {
    width: 1200px; height: 985px;
    display: flex; flex-direction: column;
    align-items: center; justify-content: center; gap: 40px;
  }
  .card {
    width: 760px; height: 434px;
    position: relative;
    box-shadow: 0 6px 18px rgba(0,0,0,.18);
  }
  .card--front { background: var(--card-dark); }
  .card--back { background: var(--card-light); color: var(--ink); }

  .wordmark {
    display: flex; align-items: center; gap: 14px;
    font-weight: 700; text-transform: uppercase;
    letter-spacing: .04em;
  }
  .wordmark__square { width: 22px; height: 22px; flex: none; }
  .card--front .wordmark {
    position: absolute; left: 50%; top: 50%;
    transform: translate(-50%, -50%);
    color: var(--on-dark); font-size: 30px; white-space: nowrap;
  }
  .card--front .wordmark__square { background: var(--on-dark); }

  .card--back .wordmark {
    position: absolute; left: 372px; top: 88px;
    color: var(--ink); font-size: 21px; white-space: nowrap;
  }
  .card--back .wordmark__square { background: var(--ink); width: 18px; height: 18px; }

  .person { position: absolute; left: 48px; top: 150px; }
  .person__name { font-weight: 700; font-size: 28px; letter-spacing: .01em; }
  .person__title { font-weight: 400; font-size: 16px; margin-top: 2px; color: var(--ink-soft); }

  .contact {
    position: absolute; left: 372px; top: 206px;
    font-size: 17px; color: var(--ink-soft); line-height: 1.3;
  }
  .contact__address { margin-bottom: 14px; padding-left: 30px; }
  .contact__list { list-style: none; }
  .contact__item { display: flex; align-items: center; gap: 12px; margin-bottom: 9px; }
  .contact__icon { width: 18px; height: 18px; flex: none; }
  .contact__plain { padding-left: 30px; }
</style>
</head>
<body>
<main class="stage">
  <section class="card card--front" aria-label="Card front">
    <div class="wordmark">
      <span class="wordmark__square"></span>
      <span>Cedar Ridge Mechanical</span>
    </div>
  </section>

  <section class="card card--back" aria-label="Card back">
    <div class="person">
      <p class="person__name">Daniel Reyes</p>
      <p class="person__title">Managing Director</p>
    </div>

    <div class="wordmark">
      <span class="wordmark__square"></span>
      <span>Cedar Ridge Mechanical</span>
    </div>

    <div class="contact">
      <p class="contact__address">245 Harbor View Road<br>Bellingham, WA 98225</p>
      <ul class="contact__list">
        <li class="contact__item">
          <svg class="contact__icon" viewBox="0 0 24 24" aria-hidden="true">
            <path fill="#1e1e1e" d="M6.6 10.8a15.1 15.1 0 0 0 6.6 6.6l2.2-2.2a1 1 0 0 1 1-.25 11.4 11.4 0 0 0 3.6.57 1 1 0 0 1 1 1V20a1 1 0 0 1-1 1A17 17 0 0 1 3 4a1 1 0 0 1 1-1h3.5a1 1 0 0 1 1 1c0 1.25.2 2.45.57 3.6a1 1 0 0 1-.25 1z"/>
          </svg>
          <span>555.214.3370</span>
        </li>
        <li class="contact__item">
          <svg class="contact__icon" viewBox="0 0 24 24" aria-hidden="true">
            <rect x="2" y="5" width="20" height="14" rx="1.5" fill="#1e1e1e"/>
            <path d="M3 6.5l9 6.5 9-6.5" fill="none" stroke="#fff" stroke-width="1.6"/>
          </svg>
          <span>info@cedarridgemechanical.com</span>
        </li>
        <li class="contact__item">
          <svg class="contact__icon" viewBox="0 0 24 24" aria-hidden="true">
            <circle cx="12" cy="12" r="10" fill="#1e1e1e"/>
            <path d="M2 12h20M12 2c3 3 3 17 0 20M12 2c-3 3-3 17 0 20" fill="none" stroke="#fff" stroke-width="1.3"/>
          </svg>
          <span>www.cedarridgemechanical.com</span>
        </li>
        <li class="contact__item contact__plain">
          <span>www.cedarridgemechanical.com</span>
        </li>
      </ul>
    </div>
  </section>
</main>
</body>
</html>
```